IT Consultancy Needs Daring Webpage (uncoded)

We are looking for a web page for a small IT firm, Harbor Linkworks. We provide remote IT services, website development and IT consultancy. We are looking for a website that is a bit unique and will look both professional and cutting edge.

We are mainly targeting high cash flow small businesses.
Feel free to play with our yellow/blue theme. We where aiming for similar colours to movie posters i.e the Crimson Ledger, http://qlink.example/x4mTz. Think metallic, flashy and classy like a colourful Zuno.
Updates

We have a website but it is very poor and we would prefer if you did not use it for inspiration.

We quite like this design http://gallery.artfoldex.net/designs/web/?order=24&offset=24#/k7p3wq9

The three cornerstones of our business are Consult, Support and E-Marketing

other designs are welcome as well (different from the the link above)

Target Market(s)

Small Businesses

Industry/Entity Type

Movie

Requirements
Must have
• Space for Home, Services, Contact and Blog menu bars.

Our logo is ok, you are welcome to adjust it a little to meet your needs.

While we appreciate most websites have a dense middle ground for navigation panels, we would like the most important buttons highlighted as well as a slightly interesting background for example, instead of a plain colour background, a slight hint of a pattern or image.
Should not have
• Should not have a banner.

```html
<!DOCTYPE html>
<html lang="en">
<head>
<meta charset="utf-8">
<title>Harbor Linkworks – Services</title>
<link rel="stylesheet" href="https://fonts.googleapis.com/css2?family=Arimo:wght@400;700&family=PT+Sans:wght@400;700&display=swap">
<style>
  :root {
    --page-bg: #ffffff;
    --sun-light: #fdf0a8;
    --sun-mid: #f6d658;
    --sun-deep: #eebf2e;
    --sky-top: #9fd4f1;
    --sky-mid: #6fc0ee;
    --sky-deep: #2aa7e8;
    --band-blue: #1479c0;
    --band-pattern: #2f8fd1;
    --nav-blue: #3aa6e6;
    --nav-dark: #1d7fc4;
    --nav-active: #e6ff4a;
    --ink: #111111;
    --ink-soft: #1b2b3a;
    --footer-bg: #000000;
    --footer-cyan: #2bb3f0;
    --tweet-orange: #f5a623;
    --tweet-yellow: #f4e04a;
    --white: #ffffff;
  }
  * { box-sizing: border-box; margin: 0; padding: 0; }
  html, body { width: 1200px; height: 778px; overflow: hidden; background: var(--page-bg); }
  body { font-family: "PT Sans", sans-serif; color: var(--ink); }

  .site {
    position: absolute; left: 41px; top: 0; width: 1118px; height: 778px;
    box-shadow: 0 0 12px rgba(0,0,0,.35);
    overflow: hidden;
  }

  /* Header */
  .masthead {
    position: absolute; left: 0; top: 0; width: 100%; height: 238px;
    background:
      radial-gradient(ellipse at 18% 30%, var(--sun-light) 0%, transparent 55%),
      linear-gradient(180deg, var(--sun-mid) 0%, var(--sun-light) 55%, var(--sun-mid) 100%);
  }
  .brand { position: absolute; left: 33px; top: 22px; display: flex; align-items: center; }
  .brand-mark {
    width: 164px; height: 164px; border-radius: 50%;
    background: #0a0a0a; border: 5px solid var(--sky-deep);
  }
  .brand-name {
    margin-left: 70px; font-family: "Arimo", sans-serif; font-weight: 700;
    font-size: 50px; color: var(--ink); letter-spacing: .5px;
  }
  .social { position: absolute; left: 940px; top: 14px; display: flex; gap: 20px; }
  .social-slot { width: 44px; height: 46px; border-radius: 8px; background: var(--nav-dark); }
  .help-button {
    position: absolute; left: 884px; top: 72px; width: 220px; height: 40px;
    border-radius: 20px; border: 2px solid var(--nav-dark);
    background: linear-gradient(180deg, #7fcaf4 0%, var(--nav-blue) 50%, var(--nav-dark) 100%);
    color: var(--white); font-family: "Arimo", sans-serif; font-weight: 700; font-size: 18px;
    display: flex; align-items: center; justify-content: center;
  }
  .help-phone {
    position: absolute; left: 884px; top: 124px; width: 220px; text-align: center;
    font-family: "Arimo", sans-serif; font-size: 25px; color: var(--ink); letter-spacing: 1px;
  }

  /* Navigation */
  .main-nav { position: absolute; left: 0; top: 189px; width: 560px; height: 49px; }
  .main-nav svg { position: absolute; inset: 0; }
  .nav-list { position: absolute; left: 19px; top: 0; height: 49px; display: flex; align-items: center; list-style: none; font-size: 18px; }
  .nav-list li { color: var(--ink); }
  .nav-list .is-active { color: var(--nav-active); }
  .nav-sep { color: var(--ink); }
  .breadcrumb { position: absolute; right: 13px; top: 211px; font-size: 13px; font-weight: 700; color: #3a2a00; }

  /* Main band */
  .content-band {
    position: absolute; left: 0; top: 238px; width: 100%; height: 414px;
    background:
      repeating-linear-gradient(90deg, transparent 0 28px, rgba(255,255,255,.08) 28px 30px),
      linear-gradient(180deg, #8ec5ec 0%, var(--band-pattern) 40%, var(--band-blue) 100%);
  }
  .service-panel {
    position: absolute; left: 13px; top: 22px; width: 1092px; height: 368px;
    border: 2px solid #bfe5fa;
    background: linear-gradient(180deg, var(--sky-top) 0%, var(--sky-mid) 55%, var(--sky-deep) 100%);
  }
  .service-title { position: absolute; left: 10px; top: 14px; font-family: "Arimo", sans-serif; font-weight: 700; font-size: 25px; }
  .service-intro { position: absolute; left: 10px; top: 54px; width: 718px; font-size: 12px; line-height: 17px; color: var(--ink-soft); }
  .service-sub { position: absolute; left: 10px; top: 172px; font-family: "Arimo", sans-serif; font-weight: 700; font-size: 19px; }
  .service-points { position: absolute; left: 18px; top: 212px; list-style: none; font-size: 12px; color: var(--ink-soft); }
  .service-points li { height: 24px; padding-left: 18px; position: relative; }
  .service-points li::before {
    content: ""; position: absolute; left: 2px; top: 4px;
    border-left: 6px solid #222; border-top: 4px solid transparent; border-bottom: 4px solid transparent;
  }
  .service-visual {
    position: absolute; left: 748px; top: 54px; width: 321px; height: 154px;
    border: 1px solid #000;
    background: radial-gradient(circle at 62% 45%, #8fb8c8 0%, #2a4455 30%, #0b0f14 70%);
  }

  /* Footer */
  .site-footer { position: absolute; left: 0; top: 652px; width: 100%; height: 126px; background: var(--footer-bg); color: var(--white); }
  .footer-name { position: absolute; left: 12px; top: 31px; font-family: "Arimo", sans-serif; font-size: 17px; color: var(--footer-cyan); }
  .footer-contact { position: absolute; left: 12px; top: 58px; font-size: 12px; font-weight: 700; line-height: 15px; }
  .footer-contact .label { color: var(--footer-cyan); }
  .footer-links { position: absolute; left: 12px; top: 97px; font-size: 11px; word-spacing: 2px; }
  .footer-links span { margin: 0 12px; }
  .tweets { position: absolute; left: 772px; top: 14px; width: 330px; }
  .tweets-icon { position: absolute; left: 0; top: 3px; width: 44px; height: 46px; border-radius: 6px; background: var(--footer-cyan); }
  .tweets-title { position: absolute; left: 56px; top: 0; font-family: "Arimo", sans-serif; font-size: 18px; color: var(--footer-cyan); }
  .tweets-text { position: absolute; left: 58px; top: 24px; width: 270px; font-size: 11px; line-height: 15px; color: var(--tweet-orange); }
  .tweets-text em { font-style: normal; color: var(--tweet-yellow); }
  .read-more {
    position: absolute; left: 58px; top: 72px; width: 90px; height: 21px; border-radius: 3px;
    background: linear-gradient(180deg, #6a6a6a, #333); color: var(--white);
    font-size: 12px; font-weight: 700; display: flex; align-items: center; justify-content: center;
  }
</style>
</head>
<body>
<div class="site">
  <header class="masthead">
    <div class="brand">
      <div class="brand-mark"></div>
      <div class="brand-name">Harbor Linkworks</div>
    </div>
    <div class="social">
      <div class="social-slot" role="img" aria-label="Social profile link"></div>
      <div class="social-slot" role="img" aria-label="Social profile link"></div>
    </div>
    <div class="help-button">CAN WE HELP YOU?</div>
    <div class="help-phone">0400 555 219</div>
  </header>

  <nav class="main-nav">
    <svg width="560" height="49" viewBox="0 0 560 49">
      <defs>
        <linearGradient id="navFill" x1="0" y1="0" x2="0" y2="1">
          <stop offset="0" stop-color="#7fcaf4"/>
          <stop offset=".5" stop-color="#3aa6e6"/>
          <stop offset="1" stop-color="#1d7fc4"/>
        </linearGradient>
      </defs>
      <path d="M0 0 H500 Q510 0 518 8 L560 49 H0 Z" fill="url(#navFill)"/>
    </svg>
    <ul class="nav-list">
      <li>Home</li>
      <li class="nav-sep" style="margin-left:37px">I</li>
      <li class="is-active" style="margin-left:37px">Services</li>
      <li class="nav-sep" style="margin-left:37px">I</li>
      <li style="margin-left:37px">Blog</li>
      <li class="nav-sep" style="margin-left:37px">I</li>
      <li style="margin-left:37px">Contact</li>
    </ul>
  </nav>
  <div class="breadcrumb">You are in Service Page</div>

  <main class="content-band">
    <section class="service-panel">
      <h1 class="service-title">SERVICE</h1>
      <p class="service-intro">Lorem ipsum dolor sit amet, consectetur adipiscing elit. Aliquam mauris nulla, interdum sit amet tristique vitae, tristique vel sapien. Ut hendrerit mollis molestie. Donec a lectus tellus. Proin justo diam, semper et consectetur eu, consectetur ac velit. Curabitur viverra mollis lacus, et laoreet ligula volutpat nec. Aliquam non ipsum nisi. Integer placerat bibendum quam, laoreet posuere libero aliquet ac. Mauris volutpat imperdiet felis consectetur molestie. Sed ut felis id est commodo auctor. Donec eget orci arcu, nec lacinia nunc. Fusce sed lectus in nibh vulputate cursus. Maecenas tortor ligula, ultrices nec lacinia id, scelerisque quis sem. Nam ac metus mi. Morbi purus leo, bibendum a facilisis eu, congue ut nisl. Sed eget lectus est. Donec lacus orci, aliquam non auctor eget, vulputate in ante.</p>
      <h2 class="service-sub">This is Sub Heading</h2>
      <ul class="service-points">
        <li>Nullam ultricies dolor nec turpis adipiscing tempus.</li>
        <li>Nulla in metus velit, dignissim mattis justo.</li>
        <li>Pellentesque nec lacus id orci varius iaculis id in lorem.</li>
        <li>Nulla condimentum lorem non orci porta imperdiet.</li>
        <li>Etiam condimentum odio quis metus feugiat accumsan.</li>
      </ul>
      <div class="service-visual" role="img" aria-label="Image of a robotic hand touching a glowing digital globe"></div>
    </section>
  </main>

  <footer class="site-footer">
    <div class="footer-name">HARBOR LINKWORKS</div>
    <div class="footer-contact">
      <div><span class="label">Tel :</span> +0400 555 219</div>
      <div><span class="label">Office Hours :</span> 9.00 am till 5.30 pm</div>
    </div>
    <div class="footer-links">Privacy Policy<span>|</span>Sitemap<span>|</span>© 2011 harborlinkworks.example | All rights reserved</div>
    <div class="tweets">
      <div class="tweets-icon"></div>
      <div class="tweets-title">Latest Tweets</div>
      <p class="tweets-text">Lorem ipsum dolor <em>sit amet,</em> consectetur <em>adipiscing elit.</em> Aliquam mauris nulla, <em>interdum sit amet</em></p>
      <div class="read-more">read more ›</div>
    </div>
  </footer>
</div>
</body>
</html>
```